Mobile Fitness snd Therapy Business Card Design

I need a business card designed for my mobile fitness and therapy business.

Please view the images that I have uploaded. I like the simplicity of the design that I have attached. I adapted it with my information

Target Market(s)

Those seeking personal training, injury rehabilitation or massage therapy.

Industry/Entity Type

Business

Contact Information for Business Card

Derek Fulham - MSc, CAT(C), RMT, CSCS, Pn2
e-mail: derek@vantrelo.com
website: www.vantrelo.com
instagram: @derek_fulham

Font styles to use
Sans Serif

Colors
3176b5
0355a3

Requirements
Must have
• "Contact us to receive a FREE assessment"
• Services offered:
• Personal Training
• Golf Fitness
• Injury Rehab
• Massage Therapy
• Yoga
Nice to have
• Consistent colours with brand
• - Dark Blue: #232837
• - Blue: #5096f0
• Consistent look/feel with the website: www.vantrelo.com

```html
<!DOCTYPE html>
<html lang="en">
<head>
<meta charset="utf-8">
<title>Vantrelo Business Card</title>
<link rel="stylesheet" href="https://fonts.googleapis.com/css2?family=Montserrat:wght@600;700&family=Roboto:wght@400&family=Roboto+Condensed:wght@700&display=swap">
<style>
  :root {
    --backdrop: #e6e7ea;
    --card-light: #f3f3f3;
    --card-dark: #232837;
    --ink-dark: #232837;
    --ink-muted: #4a4e5a;
    --brand-blue: #2f5fd6;
    --accent-blue: #5096f0;
    --white: #ffffff;
  }
  * { box-sizing: border-box; margin: 0; padding: 0; }
  html, body { width: 1200px; height: 960px; overflow: hidden; }
  body { background: var(--backdrop); position: relative; font-family: "Roboto", Arial, sans-serif; }

  .card {
    position: absolute;
    width: 600px;
    height: 343px;
    border-radius: 20px;
    box-shadow: 0 3px 6px rgba(0,0,0,0.25);
  }
  .card--front { left: 314px; top: 113px; background: var(--card-light); }
  .card--back { left: 311px; top: 472px; background: var(--card-dark); }

  .wordmark {
    position: absolute;
    font-family: "Montserrat", Arial, sans-serif;
    font-weight: 700;
    font-size: 44px;
    line-height: 1;
    letter-spacing: 3px;
  }
  .tagline {
    position: absolute;
    font-family: "Montserrat", Arial, sans-serif;
    font-weight: 700;
    font-size: 14px;
    letter-spacing: 2.1px;
    line-height: 1;
    white-space: nowrap;
  }
  .card--front .wordmark { left: 47px; top: 53px; color: var(--ink-dark); }
  .card--front .tagline { left: 48px; top: 98px; color: var(--ink-dark); }

  .contact-list { position: absolute; left: 48px; top: 236px; list-style: none; }
  .contact-list li {
    display: flex; align-items: center; gap: 8px;
    height: 19.5px; font-size: 14px; color: var(--ink-muted);
  }
  .contact-list svg { width: 14px; height: 14px; flex: none; }

  .person { position: absolute; right: 48px; top: 247px; text-align: right; font-family: "Roboto Condensed", Arial, sans-serif; font-weight: 700; color: var(--brand-blue); }
  .person__name { font-size: 22px; line-height: 1; }
  .person__credentials { font-size: 11px; margin-top: 3px; }

  .card--back .wordmark { left: 0; width: 600px; text-align: center; top: 130px; color: var(--white); }
  .card--back .tagline { left: 0; width: 600px; text-align: center; top: 182px; color: var(--white); }

  .offer {
    position: absolute; left: 58px; top: 258px; width: 483px; height: 33px;
    border-radius: 17px; background: var(--brand-blue); color: var(--white);
    font-family: "Roboto Condensed", Arial, sans-serif; font-weight: 700; font-size: 20px;
    display: flex; align-items: center; justify-content: center;
  }
  .services {
    position: absolute; left: 0; width: 600px; top: 297px; text-align: center;
    color: var(--white); font-size: 14.5px; white-space: nowrap;
  }
  .services .divider { color: var(--accent-blue); margin: 0 3px; }
</style>
</head>
<body>
  <section class="card card--front" aria-label="Card front">
    <div class="wordmark">VANTRELO</div>
    <div class="tagline">NUTRITION - FITNESS - HEALTH</div>

    <ul class="contact-list">
      <li>
        <svg viewBox="0 0 14 14" aria-hidden="true"><rect x="1" y="3" width="12" height="8" rx="1" fill="var(--brand-blue)"/><path d="M1.5 3.5 7 7.5 12.5 3.5" stroke="#fff" stroke-width="1.2" fill="none"/></svg>
        derek@vantrelo.com
      </li>
      <li>
        <svg viewBox="0 0 14 14" aria-hidden="true"><circle cx="7" cy="7" r="6" fill="var(--brand-blue)"/><path d="M1 7h12M7 1c-2.5 3-2.5 9 0 12M7 1c2.5 3 2.5 9 0 12" stroke="#fff" stroke-width="0.9" fill="none"/></svg>
        www.vantrelo.com
      </li>
      <li>
        <svg viewBox="0 0 14 14" aria-hidden="true"><circle cx="7" cy="7" r="6.5" fill="var(--brand-blue)"/></svg>
        @derek_fulham
      </li>
    </ul>

    <div class="person">
      <div class="person__name">DEREK FULHAM</div>
      <div class="person__credentials">MSC, CAT(C), RMT, CSCS, PN2</div>
    </div>
  </section>

  <section class="card card--back" aria-label="Card back">
    <div class="wordmark">VANTRELO</div>
    <div class="tagline">NUTRITION - FITNESS - HEALTH</div>
    <div class="offer">CONTACT US TO RECEIVE A FREE ASSESSMENT</div>
    <p class="services">Personal Training<span class="divider">|</span>Golf Fitness<span class="divider">|</span>Injury Rehab<span class="divider">|</span>Massage Therapy<span class="divider">|</span>Yoga</p>
  </section>
</body>
</html>
```